larkforge website

commerce website to sell cookeries, brackets, mailboxes and to show off homes built. Modern Steel in design see marlo cycles web page to be like: https://www.marlocycles-demo.com/en/ sorry its bright nest hosting word press divi

must be able to add products to page

Target Market(s)

mainly western states of U.S.

Industry/Entity Type

Building Product

Coding

Coded - Design and coding required

Number of Pages Required

3 page

Font styles to use
Sans Serif

Colors

Designer to choose colors to be used in the design.

Requirements
Must have
• customers to be able to order products from page
• bright nest hosting word press divi

```html
<!DOCTYPE html>
<html lang="en">
<head>
<meta charset="utf-8">
<title>Larkforge – Cookeries Steel</title>
<link href="https://fonts.googleapis.com/css2?family=Poppins:wght@300;400;500;600;700&display=swap" rel="stylesheet">
<style>
:root{
  --blue:#3e5b8c;
  --blue-dark:#324c78;
  --ink:#1d1d1d;
  --text:#555;
  --muted:#888;
  --line:#e4e4e4;
  --card:#f5f5f5;
  --hero:#ececec;
  --dark:#2e2e2e;
  --gold:#f3a81b;
  --white:#fff;
}
*{box-sizing:border-box;margin:0;padding:0}
html,body{width:1200px;height:4979px;overflow:hidden}
body{font-family:'Poppins',sans-serif;color:var(--ink);background:var(--white);position:relative}
.abs{position:absolute}
.photo{position:absolute}
.btn{position:absolute;display:flex;align-items:center;justify-content:center;font-size:11px;font-weight:600;letter-spacing:.5px;text-transform:uppercase}
.btn-blue{background:var(--blue);color:var(--white)}
.btn-outline{border:1.5px solid #bbb;color:var(--ink);background:var(--white)}
.section-title{position:absolute;left:0;width:1200px;text-align:center;font-size:42px;font-weight:300;letter-spacing:1px;text-transform:uppercase}

.topbar{top:0;left:0;width:1200px;height:39px;background:var(--blue);color:var(--white);font-size:11px}
.topbar .ship{left:87px;top:12px}
.topbar .cur{right:92px;top:12px;display:flex;align-items:center;gap:6px}
.flag{width:18px;height:18px;border-radius:50%;background:linear-gradient(#d44 0 50%,#fff 50%);border:1px solid #fff}

.header{top:39px;left:0;width:1200px;height:98px;border-bottom:1px solid var(--line)}
.logo{display:flex;align-items:center;gap:10px;color:var(--blue);font-weight:600;font-size:22px}
.logo .mark{width:30px;height:30px;border-radius:50%;background:var(--blue)}
.search{left:454px;top:31px;width:420px;height:40px;border:1px solid #ddd;border-radius:20px;display:flex;align-items:center;font-size:11px;color:var(--muted)}
.search .cat{width:130px;padding-left:20px;border-right:1px solid #ddd;color:#444}
.search .ph{padding-left:20px;flex:1}
.search .go{width:30px;height:30px;border-radius:50%;background:#ddd;margin-right:6px}
.hicons{left:916px;top:38px;display:flex;align-items:center;gap:28px;font-size:13px;font-weight:600}
.cartnum{display:inline-block;width:18px;height:18px;border-radius:50%;background:var(--blue);color:#fff;font-size:10px;text-align:center;line-height:18px;margin-right:6px}

.nav{top:137px;left:0;width:1200px;height:51px;font-size:12px;font-weight:500}
.nav span{position:absolute;top:19px;text-transform:uppercase}
.nav .active{color:var(--blue)}
.nav .active::before{content:"";position:absolute;left:-3px;right:-3px;top:-19px;height:2px;background:var(--blue)}

.hero{top:188px;left:0;width:1200px;height:585px;background:var(--hero);overflow:hidden}
.hero .shade{left:0;top:0;width:1200px;height:585px}
.hero .kicker{left:87px;top:174px;font-size:33px;font-weight:400}
.hero h1{position:absolute;left:85px;top:200px;font-size:76px;font-weight:400;letter-spacing:1px;line-height:1.2}
.hero p{position:absolute;left:87px;top:293px;width:480px;font-size:14px;line-height:23px;color:#333}
.dots{left:576px;top:541px;display:flex;gap:8px}
.dots i{width:9px;height:9px;border-radius:50%;border:1.5px solid #777;display:block}
.dots i.on{background:#444;border-color:#444}

.catcard{top:862px;height:340px;background:var(--card)}
.catcard h3{position:absolute;left:34px;top:250px;font-size:30px;font-weight:300;text-transform:uppercase}
.catcard .more{position:absolute;left:34px;top:293px;font-size:11px;font-weight:600;display:flex;align-items:center;gap:10px}

.who h2{position:absolute;left:690px;top:1398px;font-size:38px;font-weight:300;text-transform:uppercase}
.who p{position:absolute;left:690px;width:430px;font-size:14px;line-height:22px;color:var(--text)}
.play{left:553px;top:1516px;width:104px;height:104px;border-radius:50%;background:#fff;box-shadow:0 4px 20px rgba(0,0,0,.15)}

.prod{top:1999px;height:369px;width:251px;background:var(--card);text-align:center}
.prod .stars{position:absolute;top:216px;left:0;width:100%;color:var(--gold);font-size:12px;letter-spacing:1px}
.prod .name{position:absolute;top:236px;left:0;width:100%;font-size:16px}
.prod .price{position:absolute;top:263px;left:0;width:100%;font-size:18px;font-weight:600;color:var(--blue)}
.prod .btn{top:297px;left:57px;width:137px;height:35px}

.offer{top:2461px;left:0;width:1200px;height:485px;background:var(--dark);overflow:hidden;color:#fff}
.offer .k{left:87px;top:134px;font-size:16px;letter-spacing:1px}
.offer .big{left:84px;top:148px;font-size:98px;font-weight:500;letter-spacing:3px}
.offer .sub{left:87px;top:263px;font-size:16px}

.art{top:3091px;width:323px;height:400px;background:#fff;box-shadow:0 6px 24px rgba(0,0,0,.08)}
.art .date{position:absolute;left:25px;top:245px;font-size:10px;font-weight:500}
.art h4{position:absolute;left:25px;top:268px;font-size:19px;font-weight:500}
.art p{position:absolute;left:25px;top:306px;width:270px;font-size:13px;line-height:19px;color:var(--text)}
.art .meta{position:absolute;left:25px;top:366px;font-size:10px;color:var(--muted);display:flex;gap:20px}
.art .arr{position:absolute;right:25px;top:362px}

.brands{top:3675px;left:87px;width:1023px;display:flex;justify-content:space-around;font-size:15px;letter-spacing:2px;color:#777;text-transform:uppercase}
.brandline{top:3750px;left:87px;width:1023px;height:1px;background:var(--line)}

.gal h2{position:absolute;left:84px;top:3890px;font-size:42px;font-weight:300;text-transform:uppercase}
.gal .badge{left:14px;top:3902px;width:50px;height:50px;background:var(--blue)}
.next{left:1140px;top:4074px;width:40px;height:40px;border-radius:50%;background:#fff;box-shadow:0 2px 10px rgba(0,0,0,.2)}

.feat{top:4310px;display:flex;gap:12px;align-items:flex-start}
.feat b{display:block;font-size:17px;font-weight:400;text-transform:uppercase;line-height:20px}
.feat small{font-size:11px;color:#444}

.footer{top:4504px;left:0;width:1200px;height:475px;background:var(--blue);color:#fff}
.news{left:663px;top:4430px;width:537px;height:145px;background:var(--blue-dark)}
.news .input{position:absolute;left:85px;top:46px;width:317px;height:53px;background:#fff;color:#777;font-size:12px;display:flex;align-items:center;padding-left:18px}
.news .send{position:absolute;left:402px;top:46px;width:45px;height:53px;background:var(--blue);display:flex;align-items:center;justify-content:center}
.fcol h5{font-size:14px;font-weight:600;letter-spacing:.5px;margin-bottom:20px}
.fcol a{display:block;font-size:12px;line-height:27px;color:#fff;text-decoration:none}
.fcol .ci{display:flex;gap:14px;font-size:12px;line-height:18px;margin-bottom:16px}
.circ{display:inline-block;width:26px;height:26px;border-radius:50%;background:rgba(255,255,255,.3);margin-right:10px}
.pay{display:inline-block;width:50px;height:30px;border-radius:4px;background:#fff;margin-right:10px}
.fline{top:4915px;left:87px;width:1023px;height:1px;background:rgba(255,255,255,.3)}
.copy{top:4940px;left:0;width:1200px;text-align:center;font-size:11px}
.totop{left:1132px;top:4903px;width:40px;height:40px;border-radius:50%;background:#fff}
</style>
</head>
<body>

<div class="abs topbar">
  <span class="abs ship">FREE SHIPPING WORLDWIDE for orders over £20</span>
  <span class="abs cur"><i class="flag"></i>Dollar (US) ▾</span>
</div>

<header class="abs header">
  <div class="abs logo" style="left:87px;top:33px"><span class="mark"></span>LARKFORGE</div>
  <div class="abs search"><span class="cat">All Categories</span><span class="ph">Search for products</span><span class="go"></span></div>
  <div class="abs hicons">
    <svg width="20" height="20" viewBox="0 0 20 20" fill="none" stroke="#333" stroke-width="1.5"><path d="M4 8a6 6 0 0 1 11-2M16 12a6 6 0 0 1-11 2"/><path d="M15 2v4h-4M5 18v-4h4"/></svg>
    <svg width="20" height="20" viewBox="0 0 20 20" fill="none" stroke="#333" stroke-width="1.5"><path d="M10 17 3 10a4 4 0 0 1 7-5 4 4 0 0 1 7 5z"/></svg>
    <span><svg width="22" height="20" viewBox="0 0 22 20" fill="none" stroke="#333" stroke-width="1.5" style="vertical-align:middle"><path d="M1 2h4l3 11h11l2-8H6"/><circle cx="9" cy="17" r="1.5"/><circle cx="17" cy="17" r="1.5"/></svg> <span class="cartnum">4</span>$458.36</span>
  </div>
</header>

<nav class="abs nav">
  <span class="active" style="left:153px">Home</span>
  <span style="left:227px">Who We Are</span>
  <span style="left:345px">Accessories</span>
  <span style="left:466px">Product</span>
  <span style="left:563px">Featured</span>
  <span style="left:661px">Shop</span>
  <span style="left:731px">Blog</span>
  <span style="left:801px">Shipping &amp; Delivery</span>
  <span style="left:965px">Contact Us</span>
</nav>

<section class="abs hero">
  <svg class="abs shade" viewBox="0 0 1200 585"><polygon points="0,0 0,585 620,585" fill="#f3f3f3"/><polygon points="0,0 700,585 1200,585 1200,0" fill="#e9e9e9"/></svg>
  <div class="abs kicker">COOKERIES STEEL</div>
  <h1>COLLECTION</h1>
  <p>Free Ground shipping For Orders Over $75.00 (Before Sales Tax) within 48 Contiguous us...</p>
  <div class="btn btn-blue" style="left:89px;top:361px;width:137px;height:46px">Shop Now</div>
  <div class="photo" role="img" aria-label="Polished steel teapot, milk jug and sugar bowl set" style="left:580px;top:63px;width:600px;height:445px;background:radial-gradient(ellipse at 55% 50%,#d8d8d8,#b5b5b5 45%,rgba(236,236,236,0) 72%)"></div>
  <div class="abs dots"><i class="on"></i><i></i><i></i></div>
</section>

<div class="abs catcard" style="left:87px;width:485px">
  <div class="photo" role="img" aria-label="Wooden and steel dish drying rack" style="left:100px;top:20px;width:285px;height:200px;background:radial-gradient(ellipse,#8a6a4a,#b79a7a 50%,rgba(245,245,245,0) 75%)"></div>
  <h3>Stand Bath</h3><span class="more">SHOP NOW <svg width="18" height="8" viewBox="0 0 18 8" fill="none" stroke="#777"><path d="M0 4h16M13 1l3 3-3 3"/></svg></span>
</div>
<div class="abs catcard" style="left:588px;width:253px">
  <div class="photo" role="img" aria-label="Steel forks wrapped in a linen napkin" style="left:20px;top:0;width:213px;height:230px;background:linear-gradient(160deg,#e0cfb0,#c9b08a 50%,rgba(245,245,245,0) 90%)"></div>
  <h3>Accessories</h3><span class="more">SHOP NOW <svg width="18" height="8" viewBox="0 0 18 8" fill="none" stroke="#777"><path d="M0 4h16M13 1l3 3-3 3"/></svg></span>
</div>
<div class="abs catcard" style="left:856px;width:254px">
  <div class="photo" role="img" aria-label="Stacked stainless steel cooking pots" style="left:10px;top:40px;width:234px;height:170px;background:radial-gradient(ellipse,#a8a8a8,#d0d0d0 50%,rgba(245,245,245,0) 75%)"></div>
  <h3>Dinner Ware</h3><span class="more">SHOP NOW <svg width="18" height="8" viewBox="0 0 18 8" fill="none" stroke="#777"><path d="M0 4h16M13 1l3 3-3 3"/></svg></span>
</div>

<section class="who">
  <div class="photo" role="img" aria-label="Stacked black frying pans with wooden handles" style="left:0;top:1289px;width:605px;height:555px;background:linear-gradient(135deg,#f1f1f1 0%,#dcdcdc 35%,#2a2a2a 60%,#1c1c1c 80%,#e9e9e9 100%)"></div>
  <div class="abs play"><svg width="104" height="104" viewBox="0 0 104 104"><polygon points="45,40 63,52 45,64" fill="#222"/></svg></div>
  <h2>Who We Are</h2>
  <p style="top:1456px">Etiam rhoncus maecenas tempus, tellus eget condim entum rhon cus sem quam semper libero sit adipisc ing sem neque sed ipsum nam quam nunc.</p>
  <p style="top:1536px">Rhoncus maecenas tempus, tellus eget condim entum rhon cus sem quam semper libero sit amet.</p>
  <p style="top:1592px">Tempus, tellus eget condim entum rhon cus sem quam semper libero sit amet adipisc ing sem neque sed ipsum nam quam nunc.</p>
  <div class="btn btn-blue" style="left:692px;top:1682px;width:153px;height:44px">Find Out More</div>
</section>

<div class="section-title" style="top:1928px">Most Popular</div>
<div class="abs prod" style="left:89px">
  <div class="photo" role="img" aria-label="Black cloche dish cover" style="left:40px;top:50px;width:171px;height:130px;background:radial-gradient(ellipse,#3a3a3a,#6a6a6a 45%,rgba(245,245,245,0) 72%)"></div>
  <div class="stars">★★★★★</div><div class="name">Product Heading Here</div><div class="price">$25.00</div><div class="btn btn-outline">Add To Cart</div>
</div>
<div class="abs prod" style="left:346px">
  <div class="photo" role="img" aria-label="Steel saucepan set" style="left:30px;top:45px;width:191px;height:140px;background:radial-gradient(ellipse,#9a9a9a,#c4c4c4 45%,rgba(245,245,245,0) 72%)"></div>
  <div class="stars">★★★★★</div><div class="name">Product Heading Here</div><div class="price">$25.00</div><div class="btn btn-outline">Add To Cart</div>
</div>
<div class="abs prod" style="left:603px">
  <div class="photo" role="img" aria-label="Steel cutlery set" style="left:30px;top:45px;width:191px;height:140px;background:radial-gradient(ellipse,#b4b4b4,#d4d4d4 45%,rgba(245,245,245,0) 72%)"></div>
  <div class="stars">★★★★★</div><div class="name">Product Heading Here</div><div class="price">$25.00</div><div class="btn btn-outline">Add To Cart</div>
</div>
<div class="abs prod" style="left:860px">
  <div class="photo" role="img" aria-label="Black cast iron skillet" style="left:30px;top:45px;width:191px;height:140px;background:radial-gradient(ellipse,#1f1f1f,#4c4c4c 45%,rgba(245,245,245,0) 72%)"></div>
  <div class="stars">★★★★★</div><div class="name">Product Heading Here</div><div class="price">$25.00</div><div class="btn btn-outline">Add To Cart</div>
</div>

<section class="abs offer">
  <div class="photo" role="img" aria-label="Gold knife, fork and spoon on a black plate" style="left:580px;top:0;width:620px;height:485px;background:radial-gradient(ellipse at 60% 45%,#8a6c32,#4a3a20 35%,#232323 70%)"></div>
  <div class="abs k">EXCLUSIVE OFFER</div>
  <div class="abs big">20% OFF</div>
  <div class="abs sub">On All Products The Offer Until For This Weekend</div>
  <div class="btn btn-blue" style="left:87px;top:303px;width:205px;height:45px">This Offer Has Expired!</div>
  <div class="btn" style="left:302px;top:303px;width:125px;height:45px;background:#fff;color:#111">Order Now</div>
</section>

<div class="section-title" style="top:3026px">Latest Article</div>
<div class="abs art" style="left:89px">
  <div class="photo" role="img" aria-label="Black frying pans against a tiled wall" style="left:0;top:0;width:323px;height:224px;background:linear-gradient(160deg,#c9dbe0,#8aa 40%,#2a2a2a 75%)"></div>
  <div class="date">25-02-2019</div><h4>Some Blog Heading Here</h4><p>Auctor nisi elit consequat ipsum nec sagittis sem nibh id</p>
  <div class="meta"><span>◉ 03</span><span>♡ 12</span></div>
  <svg class="arr" width="18" height="10" viewBox="0 0 18 10" fill="none" stroke="#999"><path d="M0 5h16M12 1l4 4-4 4"/></svg>
</div>
<div class="abs art" style="left:439px">
  <div class="photo" role="img" aria-label="Pots and pans in a rustic kitchen" style="left:0;top:0;width:323px;height:224px;background:linear-gradient(160deg,#5a5048,#9a6a40 40%,#2c2c2c 80%)"></div>
  <div class="date">25-02-2019</div><h4>Some Blog Heading Here</h4><p>Auctor nisi elit consequat ipsum nec sagittis sem nibh id</p>
  <div class="meta"><span>◉ 03</span><span>♡ 12</span></div>
  <svg class="arr" width="18" height="10" viewBox="0 0 18 10" fill="none" stroke="#999"><path d="M0 5h16M12 1l4 4-4 4"/></svg>
</div>
<div class="abs art" style="left:789px">
  <div class="photo" role="img" aria-label="Close-up of stainless steel pots" style="left:0;top:0;width:323px;height:224px;background:linear-gradient(160deg,#e0e0e0,#8a8a8a 45%,#3a3a3a 85%)"></div>
  <div class="date">25-02-2019</div><h4>Some Blog Heading Here</h4><p>Auctor nisi elit consequat ipsum nec sagittis sem nibh id</p>
  <div class="meta"><span>◉ 03</span><span>♡ 12</span></div>
  <svg class="arr" width="18" height="10" viewBox="0 0 18 10" fill="none" stroke="#999"><path d="M0 5h16M12 1l4 4-4 4"/></svg>
</div>

<div class="section-title" style="top:3574px">Shop By Brands</div>
<div class="abs brands"><span>Oldmill</span><span>Trueform</span><span>Brewline</span><span>Ironleaf</span><span>Kettlecraft</span></div>
<div class="abs brandline"></div>

<section class="gal">
  <div class="abs badge"></div>
  <h2>Pixlane</h2>
  <div class="photo" role="img" aria-label="Black enamel cookware stack" style="left:89px;top:3978px;width:201px;height:236px;background:linear-gradient(160deg,#8a4a3a,#2a2a2a 55%,#1a1a1a)"></div>
  <div class="photo" role="img" aria-label="Silver forks on a white plate" style="left:294px;top:3978px;width:201px;height:236px;background:linear-gradient(160deg,#2a2a2a,#bcbcbc 50%,#e6e6e6)"></div>
  <div class="photo" role="img" aria-label="Steel pot rims close-up" style="left:499px;top:3978px;width:202px;height:236px;background:linear-gradient(160deg,#3a3a3a,#a8a8a8 50%,#2a2a2a)"></div>
  <div class="photo" role="img" aria-label="Cutlery in a steel holder" style="left:705px;top:3978px;width:201px;height:236px;background:linear-gradient(160deg,#1c1c1c,#4a4a4a 55%,#222)"></div>
  <div class="photo" role="img" aria-label="Knife and fork on a dark napkin" style="left:910px;top:3978px;width:201px;height:236px;background:linear-gradient(160deg,#444,#777 50%,#333)"></div>
  <div class="photo" role="img" aria-label="White marble surface" style="left:1115px;top:3978px;width:85px;height:236px;background:linear-gradient(160deg,#eee,#d8d8d8)"></div>
  <div class="abs next"><svg width="40" height="40" viewBox="0 0 40 40" fill="none" stroke="#222" stroke-width="1.5"><path d="M18 15l5 5-5 5"/></svg></div>
</section>

<div class="abs feat" style="left:168px">
  <svg width="36" height="32" viewBox="0 0 36 32" fill="none" stroke="var(--blue)" stroke-width="2"><rect x="2" y="8" width="32" height="22"/><path d="M2 8l16 12 16-12M8 8V2h20v6"/></svg>
  <div><b>Contact Us</b><small>hello@larkforge-demo.com</small></div>
</div>
<div class="abs feat" style="left:390px">
  <svg width="44" height="32" viewBox="0 0 44 32" fill="var(--blue)"><rect x="0" y="4" width="26" height="20"/><path d="M28 10h9l6 8v6H28z"/><circle cx="9" cy="27" r="4"/><circle cx="35" cy="27" r="4"/></svg>
  <div><b>Free Shipping</b><small>on orders over £20</small></div>
</div>
<div class="abs feat" style="left:628px">
  <svg width="34" height="36" viewBox="0 0 34 36" fill="none" stroke="var(--blue)" stroke-width="2.5"><path d="M4 11h26l-2 22H6z"/><path d="M11 11V8a6 6 0 0 1 12 0v3"/></svg>
  <div><b>Shop Pixlane</b><small>See. Tap. Shop.</small></div>
</div>
<div class="abs feat" style="left:893px">
  <svg width="36" height="36" viewBox="0 0 36 36"><rect width="36" height="36" fill="var(--blue)"/></svg>
  <div><b>Connect</b><small>On Circlebook</small></div>
</div>

<footer class="abs footer"></footer>
<div class="abs news">
  <div class="input">✉&nbsp;&nbsp;Enter your email address...</div>
  <div class="send"><svg width="16" height="16" viewBox="0 0 16 16" fill="#fff"><path d="M1 8 15 1 11 15 8 9z"/></svg></div>
</div>
<div class="abs logo" style="left:87px;top:4720px;color:#fff;font-size:30px;font-weight:500"><span class="mark" style="background:#fff;width:40px;height:40px"></span>LARKFORGE</div>
<div class="abs fcol" style="left:414px;top:4662px">
  <h5>INFORMATION</h5>
  <a>About Us</a><a>Delivery</a><a>Store</a><a>Terms &amp; Conditions</a><a>Policies</a><a>Shop Pixlane</a>
</div>
<div class="abs fcol" style="left:638px;top:4662px">
  <h5>CONTACT US</h5>
  <div class="ci"><span>✉</span><span>Email:<br>shop@larkforge-demo.com</span></div>
  <div class="ci"><span>☏</span><span>Phone:<br>123-456-7890</span></div>
  <div class="ci"><svg width="12" height="16" viewBox="0 0 12 16" fill="#fff"><path d="M6 0a6 6 0 0 1 6 6c0 4-6 10-6 10S0 10 0 6a6 6 0 0 1 6-6z"/></svg><span>Office Location:<br>Some address line goes here</span></div>
</div>
<div class="abs fcol" style="left:885px;top:4662px">
  <h5>LET'S GET SOCIAL</h5>
  <div><span class="circ"></span><span class="circ"></span><span class="circ"></span></div>
  <h5 style="margin:36px 0 18px">PAYMENT METHODS</h5>
  <div><span class="pay"></span><span class="pay"></span><span class="pay"></span><span class="pay"></span></div>
</div>
<div class="abs fline"></div>
<div class="abs copy">© 2020. LARKFORGE. ALL RIGHTS RESERVED</div>
<div class="abs totop"><svg width="40" height="40" viewBox="0 0 40 40" fill="none" stroke="#222" stroke-width="1.5"><path d="M20 27V13M15 18l5-5 5 5"/></svg></div>

</body>
</html>
```